Landing Page & Email Signature

I am looking for a new landing page as well as an email signature to align with the change in business. I have included the new logo/emblem which I'd like incorporated into the design and the current landing page is www.delmorquivex.com.au should you wish to see the old version.

```html
<!DOCTYPE html>
<html lang="en">
<head>
<meta charset="utf-8">
<title>Kestrova Freight</title>
<link href="https://fonts.googleapis.com/css2?family=Russo+One&family=Poppins:wght@400;500;600;700&display=swap" rel="stylesheet">
<style>
:root{
  --red:#c8102e;
  --red-dark:#8e0a1f;
  --ink:#1d1d22;
  --grey:#55575e;
  --light:#f4f4f6;
  --night:#202229;
  --black:#0c0c0e;
  --white:#ffffff;
}
*{box-sizing:border-box;margin:0;padding:0}
html,body{width:1200px;height:4368px;overflow:hidden}
body{position:relative;background:var(--white);font-family:"Poppins",sans-serif;color:var(--ink)}
.abs{position:absolute}
.title{font-family:"Russo One",sans-serif;font-size:40px;color:var(--red);text-align:center;letter-spacing:1px}
.title span{color:var(--ink)}
.lead{font-size:15px;line-height:24px;color:var(--grey);text-align:center}
.lead b{color:var(--red);font-weight:600}
.btn{display:inline-flex;align-items:center;gap:12px;height:40px;padding:0 8px 0 22px;border-radius:4px;font-size:13px;font-weight:600;letter-spacing:.5px;text-transform:uppercase;white-space:nowrap}
.btn-red{background:var(--red);color:var(--white)}
.btn-line{border:2px solid var(--red);color:var(--red);background:var(--white);padding:0 22px}
.btn .dot{width:26px;height:26px;border-radius:50%;background:var(--white);display:flex;align-items:center;justify-content:center}
.brand{display:flex;align-items:center;gap:10px;font-family:"Russo One",sans-serif;color:var(--white);font-size:24px;white-space:nowrap}
.brand i{width:18px;height:18px;border-radius:50%;background:var(--red);display:block}

/* hero */
.hero{left:0;top:0;width:1200px;height:620px;background:linear-gradient(180deg,#2b3038 0%,#4a4f56 45%,#6d3236 75%,#2a2b31 100%)}
.nav{left:120px;top:20px;width:960px;display:flex;align-items:center;justify-content:space-between}
.nav ul{display:flex;gap:34px;list-style:none;color:var(--white);font-size:13px;font-weight:600}
.nav .phone{border:1px solid rgba(255,255,255,.7);border-radius:4px;color:var(--white);font-size:13px;padding:8px 14px}
.hero-title{left:0;top:238px;width:1200px;text-align:center;font-family:"Russo One",sans-serif;font-size:58px;line-height:70px;color:var(--white);letter-spacing:2px}
.hero-tag{left:0;top:318px;width:1200px;text-align:center;font-size:16px;line-height:22px;font-weight:700;color:var(--white);letter-spacing:1px}
.hero-cta{left:0;top:362px;width:1200px;display:flex;justify-content:center}
.social{left:1128px;top:460px;display:flex;flex-direction:column;gap:10px}
.social i{width:18px;height:18px;border:1px solid rgba(255,255,255,.7);border-radius:50%;display:block}
.dots{left:580px;top:584px;display:flex;gap:6px}
.dots i{width:12px;height:4px;background:rgba(255,255,255,.5);display:block}.dots i:first-child{background:var(--white)}

/* services */
.card{width:306px;height:222px;background:linear-gradient(135deg,#6f7680,#3b4048);overflow:hidden;border-radius:2px}
.card .label{position:absolute;left:0;bottom:0;width:100%;height:38px;background:rgba(12,12,14,.85);color:var(--white);font-size:12px;font-weight:600;display:flex;align-items:center;justify-content:space-between;padding:0 14px;text-transform:uppercase}
.card.focus .over{position:absolute;inset:0;background:rgba(28,28,32,.82);color:var(--white);text-align:center;padding:50px 30px 0;font-size:11px;line-height:17px}
.card.focus .over h4{color:var(--red);font-size:13px;margin-bottom:6px;text-transform:uppercase}

/* blog */
.blog{left:0;top:1965px;width:1200px;height:700px;background:var(--night);overflow:hidden}
.post{width:440px;height:410px;background:var(--white);border-radius:6px;overflow:hidden}
.post .img{height:200px;margin:10px;border-radius:4px}
.post h3{font-size:19px;line-height:25px;font-weight:700;padding:6px 20px 0}
.post p{font-size:12px;line-height:18px;color:var(--grey);padding:8px 20px}
.post a{display:block;padding:6px 20px;color:var(--red);font-size:13px;font-weight:600;font-style:italic}

/* experience */
.partner{width:150px;height:44px;display:flex;align-items:center;justify-content:center}
.partner i{display:block;background:#c5c7cd}

/* contact */
.contact{left:0;top:3440px;width:1200px;height:575px;background:linear-gradient(100deg,#b10e28 0%,#c8102e 55%,#a53a44 80%,#7f5a5e 100%)}
.field{background:var(--white);height:38px;border-radius:2px;font-size:11px;color:#8a8c92;padding:0 14px;display:flex;align-items:center;gap:8px;text-transform:uppercase}
.field i{width:9px;height:9px;border-radius:50%;background:var(--red);display:block}

/* footer */
.footer{left:0;top:4015px;width:1200px;height:353px;background:var(--black);color:var(--white)}
.fcol h5{font-size:15px;font-weight:700;letter-spacing:1px;margin-bottom:14px}
.fcol li{list-style:none;font-size:12px;line-height:20px;color:#d6d6d9;text-transform:uppercase}
.contact-line{display:flex;gap:10px;align-items:flex-start;font-size:12px;line-height:18px;margin-bottom:12px;color:#d6d6d9}
</style>
</head>
<body>

<!-- HERO -->
<section class="hero abs" role="img" aria-label="Red freight trucks driving along a highway at dusk"></section>
<nav class="nav abs">
  <div class="brand"><i></i>KESTROVA FREIGHT</div>
  <ul><li>COMPANY</li><li>ABOUT US</li><li>GLOBAL COVERAGE</li><li>BLOG</li><li>CONTACT</li></ul>
  <div class="phone">+1 (555) 014 2290</div>
</nav>
<h1 class="hero-title abs">KESTROVA FREIGHT</h1>
<p class="hero-tag abs">PROVIDING FIRST CLASS FREIGHT SERVICES</p>
<div class="hero-cta abs"><span class="btn btn-red">Get Started <span class="dot"><svg width="12" height="12" viewBox="0 0 12 12"><path d="M2 6h8M7 3l3 3-3 3" stroke="#c8102e" stroke-width="1.6" fill="none"/></svg></span></span></div>
<div class="social abs"><i></i><i></i><i></i></div>
<div class="dots abs"><i></i><i></i></div>

<!-- ABOUT -->
<h2 class="title abs" style="left:0;top:700px;width:1200px">ABOUT <span>US</span></h2>
<p class="lead abs" style="left:120px;top:770px;width:960px">Perspiciatis unde omnis iste natus error sit voluptatem accusantium doloremque laudantium, totam rem aperiam, eaque ipsa quae ab illo inventore veritatis et quasi architecto beatae vitae <b>dicta sunt explicabo. Nemo enim ipsam voluptatem quia voluptas sit aspernatur aut odit aut fugit, sed quia consequuntur</b> magni dolores eos qui ratione voluptatem sequi nesciunt. Neque porro quisquam est, qui dolorem ipsum quia dolor sit amet, consectetur, adipisci velit, sed quia non numquam eius modi tempora incidunt ut labore et dolore magnam aliquam.</p>
<div class="abs" style="left:0;top:930px;width:1200px;display:flex;justify-content:center"><span class="btn btn-red">Learn More <span class="dot"><svg width="12" height="12" viewBox="0 0 12 12"><path d="M2 6h8M7 3l3 3-3 3" stroke="#c8102e" stroke-width="1.6" fill="none"/></svg></span></span></div>
<svg class="abs" style="left:110px;top:1052px" width="980" height="30"><line x1="0" y1="15" x2="980" y2="15" stroke="#b9bbc1" stroke-width="2"/><rect x="478" y="3" width="24" height="24" rx="12" fill="#fff" stroke="#b9bbc1" stroke-width="2"/><path d="M490 9v12" stroke="#55575e" stroke-width="2"/></svg>

<!-- SERVICES -->
<h2 class="title abs" style="left:0;top:1145px;width:1200px">OUR <span>SERVICES</span></h2>
<div class="card abs" style="left:112px;top:1230px" role="img" aria-label="Cranes loading cargo containers at a port"><div class="label">Professional Cranage Services<span>→</span></div></div>
<div class="card focus abs" style="left:447px;top:1230px" role="img" aria-label="Logistics warehouse"><div class="over"><h4>Cranage Services</h4>Perspiciatis unde omnis iste natus error sit voluptatem accusantium doloremque laudantium totam rem aperiam eaque ipsa quae.</div><div class="label">Learn More<span>→</span></div></div>
<div class="card abs" style="left:782px;top:1230px" role="img" aria-label="Truck backed up to a lit loading dock"><div class="label">Logistics Services Provider<span>→</span></div></div>
<div class="card abs" style="left:112px;top:1525px;background:linear-gradient(135deg,#bcc8d6,#6c7a8c)" role="img" aria-label="Business handshake in front of a freight map"><div class="label">Transport Consultancy<span>→</span></div></div>
<div class="card abs" style="left:447px;top:1525px;background:linear-gradient(135deg,#5f8fc2,#b0283a)" role="img" aria-label="Stacked cargo containers seen from above"><div class="label">Cargo Storage<span>→</span></div></div>
<div class="card abs" style="left:782px;top:1525px;background:linear-gradient(180deg,#9ab6d3,#3b5a7c)" role="img" aria-label="Container ship at sea"><div class="label">Ocean Cargo<span>→</span></div></div>
<div class="abs" style="left:0;top:1826px;width:1200px;display:flex;justify-content:center;gap:14px">
  <span class="btn btn-red">Request A Services <span class="dot"><svg width="12" height="12" viewBox="0 0 12 12"><path d="M2 6h8M7 3l3 3-3 3" stroke="#c8102e" stroke-width="1.6" fill="none"/></svg></span></span>
  <span class="btn btn-line">Contact Us</span>
</div>

<!-- BLOG -->
<section class="blog abs">
  <svg class="abs" style="left:0;top:0" width="1200" height="700"><polygon points="0,0 380,0 520,700 0,700" fill="#c8102e"/><polygon points="0,0 260,0 330,700 0,700" fill="#a70c25"/></svg>
</section>
<h2 class="title abs" style="left:0;top:2060px;width:1200px;color:var(--red)">OUR <span style="color:#fff">BLOG</span></h2>
<article class="post abs" style="left:155px;top:2140px">
  <div class="img" role="img" aria-label="Truck speeding along a road with motion blur" style="background:linear-gradient(135deg,#1f5f9e,#a9d3f0)"></div>
  <h3>Jakmeis iste natus error sitvoleptatem accusantium doloremque</h3>
  <p>Perspiciatis unde omnis iste natus error sit voluptatem accusantium doloremque laudantium totam rem aperiam eaque ipsa quae.</p>
  <a>LEARN MORE →</a>
</article>
<article class="post abs" style="left:605px;top:2140px">
  <div class="img" role="img" aria-label="Container terminal with cranes at sunset" style="background:linear-gradient(135deg,#d58a4c,#3f5f7a)"></div>
  <h3>Jakmeis iste natus error sitvoleptatem accusantium doloremque</h3>
  <p>Perspiciatis unde omnis iste natus error sit voluptatem accusantium doloremque laudantium totam rem aperiam eaque ipsa quae.</p>
  <a>LEARN MORE →</a>
</article>
<div class="abs" style="left:0;top:2582px;width:1200px;display:flex;justify-content:center"><span class="btn btn-red">View More <span class="dot"><svg width="12" height="12" viewBox="0 0 12 12"><path d="M2 6h8M7 3l3 3-3 3" stroke="#c8102e" stroke-width="1.6" fill="none"/></svg></span></span></div>

<!-- EXPERIENCE -->
<div class="abs" role="img" aria-label="Faint warehouse shelving photo" style="left:800px;top:2700px;width:400px;height:740px;background:linear-gradient(90deg,#fff,#eceaee)"></div>
<h2 class="title abs" style="left:0;top:2765px;width:1200px;color:var(--ink)">20 YEARS <span>EXPERIENCE</span></h2>
<p class="abs" style="left:150px;top:2830px;width:900px;text-align:center;font-size:17px;line-height:24px;font-weight:500;color:var(--grey)">PERSPICIATIS UNDEOMNIS ISTENATUS ERRORSIT VOLUPTATEM ACCUSANTIUM DOLOREMQUE LAUDANTIUM TOTAMREM APERIAMEAQUE IPSAQUAE ABILLO INVENTORE VERITATIST.</p>
<p class="lead abs" style="left:120px;top:2900px;width:960px">Perspiciatis unde omnis iste natus error sit voluptatem accusantium doloremque laudantium, totam rem aperiam, eaque ipsa quae ab illo inventore veritatis et quasi architecto beatae vitae <b>dicta sunt explicabo. Nemo enim ipsam voluptatem quia voluptas sit aspernatur aut odit aut fugit, sed quia consequuntur</b> magni dolores eos qui ratione voluptatem sequi nesciunt.</p>
<svg class="abs" style="left:110px;top:3075px" width="980" height="20"><line x1="0" y1="10" x2="370" y2="10" stroke="#8a8c92"/><line x1="610" y1="10" x2="980" y2="10" stroke="#8a8c92"/><text x="490" y="15" text-anchor="middle" font-family="Poppins,sans-serif" font-size="15" font-weight="700" letter-spacing="3" fill="#1d1d22">PARTNERS</text></svg>
<div class="abs" style="left:105px;top:3150px;width:990px;display:flex;justify-content:space-between">
  <div class="partner"><i style="width:40px;height:40px;border-radius:50%"></i></div>
  <div class="partner"><i style="width:40px;height:40px;border-radius:6px"></i></div>
  <div class="partner"><i style="width:40px;height:40px;border-radius:50%"></i></div>
  <div class="partner"><i style="width:40px;height:40px;border-radius:6px"></i></div>
  <div class="partner"><i style="width:40px;height:40px;border-radius:50%"></i></div>
</div>
<div class="abs" style="left:0;top:3265px;width:1200px;display:flex;justify-content:center;gap:14px">
  <span class="btn btn-red">Request A Call <span class="dot"><svg width="12" height="12" viewBox="0 0 12 12"><path d="M2 6h8M7 3l3 3-3 3" stroke="#c8102e" stroke-width="1.6" fill="none"/></svg></span></span>
  <span class="btn btn-line">Request Success Stories</span>
</div>

<!-- CONTACT -->
<section class="contact abs" role="img" aria-label="Warehouse racking faded into a red overlay"></section>
<h2 class="title abs" style="left:0;top:3480px;width:1200px;color:#fff">CONTACT <span style="color:#fff">US</span></h2>
<p class="abs" style="left:230px;top:3548px;width:740px;text-align:center;font-size:17px;line-height:24px;font-weight:500;color:#fff">Perspiciatis undeomnis istenatus errorsit voluptatem accusantium doloremque laudantium totamrem aperiameaque ipsaquae abillo inventore veritatist.</p>
<div class="field abs" style="left:240px;top:3625px;width:355px"><i></i>First Name</div>
<div class="field abs" style="left:605px;top:3625px;width:355px"><i></i>Last Name</div>
<div class="field abs" style="left:240px;top:3675px;width:355px"><i></i>Email</div>
<div class="field abs" style="left:605px;top:3675px;width:355px"><i></i>Phone</div>
<div class="field abs" style="left:240px;top:3725px;width:720px;height:120px;align-items:flex-start;padding-top:12px"><i></i>Message</div>
<div class="abs" style="left:0;top:3870px;width:1200px;display:flex;justify-content:center"><span class="btn btn-red" style="background:#fff;color:var(--red)">Submit <span class="dot" style="background:var(--red)"><svg width="12" height="12" viewBox="0 0 12 12"><path d="M2 6h8M7 3l3 3-3 3" stroke="#fff" stroke-width="1.6" fill="none"/></svg></span></span></div>

<!-- FOOTER -->
<footer class="footer abs">
  <div class="brand abs" style="left:110px;top:80px;font-size:20px"><i></i>KESTROVA FREIGHT</div>
  <div class="abs" style="left:160px;top:130px;display:flex;gap:8px">
    <svg width="22" height="22"><circle cx="11" cy="11" r="10" fill="none" stroke="#888"/></svg>
    <svg width="22" height="22"><circle cx="11" cy="11" r="10" fill="none" stroke="#888"/></svg>
    <svg width="22" height="22"><circle cx="11" cy="11" r="10" fill="none" stroke="#888"/></svg>
  </div>
  <div class="fcol abs" style="left:355px;top:50px"><h5>QUICK LINKS</h5><ul><li>Home</li><li>Company</li><li>About Us</li><li>Global Coverage</li><li>Blog</li></ul></div>
  <div class="fcol abs" style="left:545px;top:50px"><h5>LINKS</h5><ul><li>Copyright</li><li>Legal</li><li>Privacy</li><li>Accessibility</li><li>Sitemap</li></ul></div>
  <div class="fcol abs" style="left:705px;top:50px"><h5>SUPPORT</h5><ul><li>Team</li><li>About Us</li><li>Careers</li><li>Our Values</li></ul></div>
  <div class="fcol abs" style="left:870px;top:50px;width:230px"><h5>CONTACT US</h5>
    <div class="contact-line"><svg width="12" height="14" viewBox="0 0 12 14"><path d="M6 13S1 8 1 5a5 5 0 0 1 10 0c0 3-5 8-5 8z" fill="#c8102e"/><circle cx="6" cy="5" r="1.8" fill="#0c0c0e"/></svg><span>48 Harlow Street, Brackenridge,<br>USA</span></div>
    <div class="contact-line"><svg width="12" height="12" viewBox="0 0 12 12"><path d="M2 1l3 0 1 3-1.5 1a6 6 0 0 0 2.5 2.5L8 6l3 1v3c-5 1-10-4-9-9z" fill="#c8102e"/></svg><span>+1 (555) 014 2290</span></div>
    <div class="contact-line"><svg width="13" height="10" viewBox="0 0 13 10"><rect x="0.5" y="0.5" width="12" height="9" fill="#c8102e"/><path d="M1 1l5.5 4.5L12 1" stroke="#0c0c0e" fill="none"/></svg><span>hello@kestrovafreight.com</span></div>
  </div>
  <div class="abs" style="left:0;top:295px;width:1200px;height:1px;background:#2b2b30"></div>
  <p class="abs" style="left:0;top:312px;width:1200px;text-align:center;font-size:13px;color:#d6d6d9">©2022, <span style="color:var(--red)">KESTROVA FREIGHT</span>. ALL RIGHTS RESERVED.</p>
  <svg class="abs" style="left:1112px;top:290px" width="36" height="36"><circle cx="18" cy="18" r="17" fill="#c8102e"/><path d="M12 21l6-6 6 6" stroke="#fff" stroke-width="2" fill="none"/></svg>
</footer>

</body>
</html>
```